Create a memorable Web Design for real estate branding

we are a Minnepolis brokerage and boutique housing specialist with over 27 years of experience in the Global furnished housing industry, servicing the Greater Los Angeles area. Specializing in “warm environments” we offer a customized approach to satisfying our guests and client’s needs by offering a wide array of options in highly desirable areas. Additionally, Lantern Dwelling Partners offers assistance and expertise to home buyers, sellers and investors.

Industry/Entity Type

Real Estate

Number of Pages Required

1 page

Font styles to use
Serif
Sans Serif
Decorative

```html
<!DOCTYPE html>
<html lang="en">
<head>
<meta charset="utf-8">
<title>Marrow Lane Real Estate</title>
<link rel="stylesheet" href="https://fonts.googleapis.com/css2?family=Cinzel:wght@400;700&family=Open+Sans:wght@400;600;700&family=Raleway:wght@700&display=swap">
<style>
:root{
  --teal:#17a58f;
  --lime:#8cc63f;
  --black:#050505;
  --ink:#222;
  --body:#333;
  --muted:#777;
  --paper:#f1f1f1;
  --line:#d6d6d6;
  --footer:#1c2128;
  --dot-a:#3b6fae;
  --dot-b:#2aa2d6;
  --dot-c:#2a86b8;
  --dot-d:#c8473a;
}
*{box-sizing:border-box;margin:0;padding:0}
html,body{width:1200px;height:2808px;overflow:hidden}
body{position:relative;font-family:"Open Sans",Arial,sans-serif;color:var(--body);background:#fff}
.abs{position:absolute}

/* top bar */
.topbar{left:0;top:0;width:1200px;height:36px;background:var(--teal);color:#fff;font-size:14px}
.topbar .contact{left:80px;top:9px;display:flex;gap:28px;align-items:center}
.topbar .contact span{display:flex;align-items:center;gap:8px}
.topbar .social{right:80px;top:6px;display:flex;gap:18px}
.topbar .social i{display:block;width:22px;height:22px;border:2px solid #fff;border-radius:50%}

/* header */
.header{left:0;top:36px;width:1200px;height:131px;background:var(--black)}
.brand{left:79px;top:32px;color:var(--teal);font-family:"Cinzel",Georgia,serif;font-weight:700;font-size:34px;line-height:40px;letter-spacing:1px}
.brand small{display:block;font-size:22px;line-height:26px;letter-spacing:3px}
.cta{left:846px;top:20px;width:277px;height:47px;background:var(--lime);color:#111;font-family:"Cinzel",Georgia,serif;font-size:17px;display:flex;align-items:center;justify-content:center}
.nav{right:77px;top:90px;display:flex;font-family:"Cinzel",Georgia,serif;font-size:16px;color:#fff}
.nav a{color:inherit;text-decoration:none;padding:0 14px;border-left:1px solid #888;line-height:18px}
.nav a:first-child{border-left:0;color:var(--lime)}
.nav a:last-child{padding-right:0}

/* hero */
.hero{left:0;top:167px;width:1200px;height:456px;background:linear-gradient(180deg,#6f9ccc 0%,#a8c4dc 40%,#8b8a85 62%,#4d6b3a 80%,#3f5a2e 100%)}
.arrow{width:30px;height:30px;border-radius:50%;display:flex;align-items:center;justify-content:center}
.arrow.prev{left:38px;background:#fff}
.arrow.next{right:38px;background:var(--lime)}
.caption{left:0;top:623px;width:1200px;height:53px;background:#2d2d2d;color:#fff;font-family:"Raleway",Arial,sans-serif;font-weight:700;font-size:25px;display:flex;align-items:center;justify-content:center}

/* welcome */
.welcome{left:0;top:676px;width:1200px;height:663px;background:var(--paper)}
.welcome h1{position:absolute;left:0;top:40px;width:1200px;text-align:center;font-family:"Cinzel",Georgia,serif;font-weight:400;font-size:32px;color:var(--ink)}
.welcome h1 em{font-style:normal;color:var(--teal)}
.welcome .lead{position:absolute;left:92px;top:112px;width:1016px;text-align:center;font-size:14px;line-height:23px}
.offer{position:absolute;top:221px;width:397px;text-align:center}
.offer .photo{width:397px;height:264px}
.offer h2{font-weight:400;font-size:18px;margin-top:16px;color:var(--ink)}
.offer p{font-size:14px;line-height:22px;margin-top:4px}

/* why */
.why{left:0;top:1339px;width:1200px;height:529px;background:#fff}
.section-title{font-family:"Cinzel",Georgia,serif;font-size:26px;color:var(--ink);font-weight:400}
.why .section-title{position:absolute;left:0;top:54px;width:1200px;text-align:center;text-transform:uppercase}
.why .rule{position:absolute;left:482px;top:101px;width:236px;height:1px;background:var(--line)}
.feature{position:absolute;width:320px;text-align:center}
.feature .ring{width:98px;height:98px;margin:0 auto;border:2px solid #222;border-radius:50%;display:flex;align-items:center;justify-content:center}
.feature .ring.on{background:var(--teal);border-color:var(--teal)}
.feature h3{font-weight:400;font-size:18px;margin-top:22px;color:#333;letter-spacing:.3px}

/* listings strip */
.strip{left:0;top:1868px;width:1200px;height:532px;background:var(--paper)}
.col-head{position:absolute;top:52px;height:46px;border-bottom:1px solid var(--line);display:flex;justify-content:space-between}
.col-head .section-title{font-size:24px}
.col-head .nav-arrows{font-size:20px;color:#777;letter-spacing:4px}
.card{position:absolute;top:120px;height:352px;background:#fff;box-shadow:0 2px 6px rgba(0,0,0,.35)}
.listing .photo{position:absolute;left:9px;top:9px;width:292px;height:158px}
.listing h4{position:absolute;left:12px;top:183px;font-weight:400;font-size:18px;color:#222}
.listing .sub{position:absolute;left:12px;top:209px;font-size:13px;color:#666}
.listing .divider{position:absolute;left:12px;right:12px;top:234px;height:1px;background:#ddd}
.tag{position:absolute;left:15px;top:248px;width:79px;height:31px;background:var(--teal);color:#fff;font-size:13px;display:flex;align-items:center;justify-content:center}
.price{position:absolute;right:16px;top:248px;color:var(--teal);font-size:23px;font-weight:600}
.specs{position:absolute;left:12px;right:12px;top:298px;height:28px;border-top:1px solid #e4e4e4;display:flex;justify-content:space-between;padding-top:10px;font-size:13px;color:#666}
.inquiry .field{position:absolute;left:12px;width:302px;height:44px;border:1px solid #d4d4d4;font-size:14px;color:#aaa;padding:10px 14px}
.submit{position:absolute;left:12px;top:298px;width:134px;height:42px;background:var(--teal);color:#fff;font-family:"Cinzel",Georgia,serif;font-size:20px;display:flex;align-items:center;justify-content:center}
.review .avatar{position:absolute;left:16px;top:26px;width:116px;height:116px;border-radius:50%;border:2px solid #999;background:linear-gradient(160deg,#7a5540,#d5a98c 55%,#6e4c3a)}
.review .who{position:absolute;left:148px;top:62px;font-family:"Cinzel",Georgia,serif;font-size:20px;line-height:22px}
.review .who b{display:block;color:var(--teal);font-weight:400}
.review .who span{color:#222}
.review .quote{position:absolute;left:18px;top:170px;width:290px;font-size:12px;line-height:21px;font-style:italic;color:#333;text-indent:30px}
.review .qmark{position:absolute;font-family:Georgia,serif;font-size:44px;color:#bbb;line-height:1}

/* footer */
.footer{left:0;top:2400px;width:1200px;height:365px;background:linear-gradient(180deg,#1a2029 0%,#2b333e 55%,#1e242c 100%)}
.footer h5{position:absolute;top:62px;font-family:"Cinzel",Georgia,serif;font-weight:400;font-size:21px;color:#fff}
.footer h5 em{font-style:normal;color:var(--lime)}
.links{position:absolute;left:81px;top:115px;list-style:none;font-size:14px;color:#fff}
.links li{height:40px}
.links li::before{content:"›";margin-right:10px;font-size:16px}
.ci{position:absolute;left:301px;display:flex;gap:14px;font-size:15px;color:#fff;line-height:21px}
.ci .ic{width:34px;height:34px;background:var(--lime);flex:none;display:flex;align-items:center;justify-content:center}
.follow{position:absolute;left:628px;top:108px;list-style:none}
.follow li{display:flex;align-items:center;gap:16px;height:53px;font-size:12px;color:#fff}
.follow i{display:block;width:38px;height:38px;border-radius:50%}
.footer-brand{position:absolute;left:846px;top:158px;font-family:"Cinzel",Georgia,serif;font-weight:700;font-size:36px;line-height:40px;color:#8a8f96;letter-spacing:1px}
.footer-brand small{display:block;font-size:24px;letter-spacing:3px}
.copy{left:0;top:2765px;width:1200px;height:43px;background:var(--teal);color:#fff;font-size:14px;display:flex;align-items:center;justify-content:center}
</style>
</head>
<body>

<div class="abs topbar">
  <div class="abs contact">
    <span><svg width="14" height="14" viewBox="0 0 24 24"><path fill="#fff" d="M6.6 10.8a15 15 0 006.6 6.6l2.2-2.2a1 1 0 011-.25 11 11 0 003.6.6 1 1 0 011 1V20a1 1 0 01-1 1A17 17 0 013 4a1 1 0 011-1h3.5a1 1 0 011 1c0 1.25.2 2.45.6 3.6a1 1 0 01-.25 1z"/></svg>555-014-2290</span>
    <span><svg width="14" height="11" viewBox="0 0 24 18"><rect width="24" height="18" fill="#fff"/><path d="M0 0l12 9 12-9" fill="none" stroke="#17a58f" stroke-width="2"/></svg>info@marrowlanehomes.example</span>
  </div>
  <div class="abs social"><i></i><i></i><i></i><i></i></div>
</div>

<header class="abs header">
  <div class="abs brand">Marrow Lane<small>Real Estate</small></div>
  <div class="abs cta">Schedule Free Consultation</div>
  <nav class="abs nav">
    <a href="#">Find a Home</a><a href="#">Sell Your Home</a><a href="#">Hearth Blog</a><a href="#">Our Agents</a><a href="#">Contact Us</a>
  </nav>
</header>

<section class="abs hero" role="img" aria-label="Photo of a single-storey suburban house with a grey roof, garage and landscaped front garden">
  <div class="abs arrow prev" style="top:233px"><svg width="10" height="12" viewBox="0 0 10 12"><path d="M7 1L2 6l5 5" fill="none" stroke="#222" stroke-width="2"/></svg></div>
  <div class="abs arrow next" style="top:233px"><svg width="10" height="12" viewBox="0 0 10 12"><path d="M3 1l5 5-5 5" fill="none" stroke="#fff" stroke-width="2"/></svg></div>
</section>
<div class="abs caption">Lantern Dwelling Partners Offers Assistance &amp; Expertise To Home Buyers, Sellers &amp; Investors.</div>

<section class="abs welcome">
  <h1>Welcome to <em>Marrow Lane Real Estate</em></h1>
  <p class="lead">Lorem ipsum dolor sit amet, consectetuer adipiscing elit, sed diam nonummy nibh euismod tincidunt ut laoreet dolore magna aliquam erat volutpat. Ut wisi enim ad minim veniam, quis nostrud exerci tation ullamcorper suscipit lobortis nisl ut aliquip ex ea commodo consequat. Duis autem vel eum iriure dolor in hendrerit in vulputate velit esse molestie consequat, vel illum dolore eu feugiat nulla facilisis at vero</p>
  <div class="offer" style="left:152px">
    <div class="photo" role="img" aria-label="Photo of a modern living room with warm lighting and a fireplace" style="background:linear-gradient(180deg,#b0713f 0%,#d9c6a8 35%,#8c7a66 70%,#5a4a3c 100%)"></div>
    <h2>BUY WITH US</h2>
    <p>Lorem ipsum dolor sit amet, consectetuer adipiscing elit, sed diam nonummy nibh euismod tincidunt ut laoreet dolore magna aliquam erat volutpat. Ut wisi enim ad minim veniam,</p>
  </div>
  <div class="offer" style="left:653px">
    <div class="photo" role="img" aria-label="Photo of a couple shaking hands with an agent outside a house" style="background:linear-gradient(180deg,#cfd8e2 0%,#9fb3c6 35%,#5f7f4c 70%,#3e5a30 100%)"></div>
    <h2>SELL WITH US</h2>
    <p>Lorem ipsum dolor sit amet, consectetuer adipiscing elit, sed diam nonummy nibh euismod tincidunt ut laoreet dolore magna aliquam erat volutpat. Ut wisi enim ad minim veniam,</p>
  </div>
</section>

<section class="abs why">
  <h2 class="section-title">Why Choose Us</h2>
  <div class="rule"></div>
  <div class="feature" style="left:98px;top:132px">
    <div class="ring on"><svg width="46" height="46" viewBox="0 0 46 46" fill="none" stroke="#fff" stroke-width="2.5"><circle cx="13" cy="9" r="5" fill="#fff"/><path d="M6 38V20h14v18M13 38V28"/><circle cx="32" cy="18" r="9"/><path d="M34.5 14h-4a2 2 0 000 4h3a2 2 0 010 4h-4M32 12v12"/></svg></div>
    <h3>A PROVEN BROKERAGE</h3>
  </div>
  <div class="feature" style="left:441px;top:132px">
    <div class="ring"><svg width="48" height="40" viewBox="0 0 48 40" fill="none" stroke="#222" stroke-width="2.5"><rect x="4" y="16" width="40" height="20"/><circle cx="24" cy="26" r="5"/><path d="M8 12h32M12 7h24"/></svg></div>
    <h3>NO JUNK FEES</h3>
  </div>
  <div class="feature" style="left:782px;top:132px">
    <div class="ring"><svg width="48" height="42" viewBox="0 0 48 42" fill="none" stroke="#222" stroke-width="2.5"><rect x="4" y="6" width="36" height="24"/><path d="M22 30v6M14 37h16"/><path d="M28 4l14 8-10 4z" fill="#222"/></svg></div>
    <h3>PROFESSIONAL MARKETING</h3>
  </div>
  <div class="feature" style="left:98px;top:317px">
    <div class="ring"><svg width="42" height="46" viewBox="0 0 42 46" fill="none" stroke="#222" stroke-width="2.5"><path d="M6 4h22v38H6z"/><path d="M11 12h12M11 18h12M11 24h8"/><path d="M36 14L22 34l-3 5 5-3 14-20z"/></svg></div>
    <h3>ELECTRONIC SIGNATURES</h3>
  </div>
  <div class="feature" style="left:441px;top:317px">
    <div class="ring"><svg width="40" height="48" viewBox="0 0 40 48" fill="none" stroke="#222" stroke-width="2.5"><rect x="8" y="4" width="20" height="36" rx="3"/><path d="M14 24l8 8 10-2v14H18l-8-8"/></svg></div>
    <h3>DIGITAL MARKETING EXPERTS</h3>
  </div>
  <div class="feature" style="left:782px;top:317px">
    <div class="ring"><svg width="50" height="46" viewBox="0 0 50 46" fill="#222"><circle cx="25" cy="20" r="6"/><path d="M15 40a10 10 0 0120 0z"/><g><circle cx="8" cy="18" r="3"/><circle cx="42" cy="18" r="3"/><circle cx="14" cy="6" r="3"/><circle cx="36" cy="6" r="3"/><circle cx="25" cy="3" r="3"/></g><path d="M8 18L25 20 42 18M14 6L25 20 36 6M25 3v17" stroke="#222" stroke-width="1.5" fill="none"/></svg></div>
    <h3>OUR VENDOR NETWORK</h3>
  </div>
</section>

<section class="abs strip">
  <div class="col-head" style="left:82px;width:320px"><h2 class="section-title">Featured Listings</h2><span class="nav-arrows">‹ ›</span></div>
  <div class="col-head" style="left:438px;width:326px"><h2 class="section-title">Quick Inquiry</h2></div>
  <div class="col-head" style="left:794px;width:326px"><h2 class="section-title">Customer Reviews</h2><span class="nav-arrows">‹ ›</span></div>

  <article class="card listing" style="left:79px;width:310px">
    <div class="photo" role="img" aria-label="Photo of a large two-storey stone house under a blue sky" style="background:linear-gradient(180deg,#3a6fb5 0%,#8fb1d6 40%,#b9b2a4 65%,#4f7a36 100%)"></div>
    <h4>123 Dollar Smit Amet</h4>
    <p class="sub">Duis autem vel eum iriure</p>
    <div class="divider"></div>
    <div class="tag">For Rent</div>
    <div class="price">$ 123, 000</div>
    <div class="specs"><span>⤢ 1200 sq ft</span><span>▭ 2 Beds</span><span>◊ 2 Baths</span></div>
  </article>

  <form class="card inquiry" style="left:438px;width:328px">
    <div class="field" style="top:14px">Your name</div>
    <div class="field" style="top:72px">Your email</div>
    <div class="field" style="top:130px">Your phone number</div>
    <div class="field" style="top:188px;height:92px">Your message</div>
    <div class="submit">Submit</div>
  </form>

  <article class="card review" style="left:794px;width:328px">
    <div class="avatar" role="img" aria-label="Portrait photo of the reviewer"></div>
    <div class="who"><b>Nora Whitfield</b><span>Designation</span></div>
    <span class="qmark" style="left:14px;top:164px">“</span>
    <p class="quote">Lorem ipsum dolor sit amet, consece dipiscing elit, sed dianonummy nibh euismod tincid ut laoreet dolore magna aliquam erat dipiscing elit, anonummy erat dipiscing elit, sed dianonummy nibh euismod nibh euismod tincidunt ut laoreet dolore m aliquam erat dipiscing elit, sed dianonummy nibh euismod volutpat. Utwisi enim ad minim.</p>
    <span class="qmark" style="left:194px;top:318px">”</span>
  </article>
</section>

<footer class="abs footer" role="img" aria-label="Dimmed photo of a city skyline at dusk behind the footer">
  <h5 style="left:81px">Quick <em>Links</em></h5>
  <ul class="links"><li>Find A Home</li><li>Sell Your Home</li><li>Hearth Blog</li><li>Our Agents</li><li>Contact Us</li></ul>

  <h5 style="left:301px">Contact <em>Details</em></h5>
  <div class="ci" style="top:112px"><span class="ic"><svg width="16" height="20" viewBox="0 0 16 20"><path fill="#fff" d="M8 0a8 8 0 00-8 8c0 6 8 12 8 12s8-6 8-12a8 8 0 00-8-8zm0 11a3 3 0 110-6 3 3 0 010 6z"/></svg></span><div><b>Office:</b><br>123. Lorem ipsum dolor<br>sit amet, consecte 32145</div></div>
  <div class="ci" style="top:200px;align-items:center"><span class="ic"><svg width="18" height="18" viewBox="0 0 24 24"><path fill="#fff" d="M6.6 10.8a15 15 0 006.6 6.6l2.2-2.2a1 1 0 011-.25 11 11 0 003.6.6 1 1 0 011 1V20a1 1 0 01-1 1A17 17 0 013 4a1 1 0 011-1h3.5a1 1 0 011 1c0 1.25.2 2.45.6 3.6a1 1 0 01-.25 1z"/></svg></span>555 014 2290</div>
  <div class="ci" style="top:258px;align-items:center;font-size:14px"><span class="ic"><svg width="18" height="13" viewBox="0 0 24 18"><rect width="24" height="18" fill="#fff"/><path d="M0 0l12 9 12-9" fill="none" stroke="#8cc63f" stroke-width="2"/></svg></span>info@marrowlanehomes.example</div>

  <h5 style="left:628px">Follow <em>Us</em></h5>
  <ul class="follow">
    <li><i style="background:var(--dot-a)"></i>FRIENDWALL</li>
    <li><i style="background:var(--dot-b)"></i>CHIRPER</li>
    <li><i style="background:var(--dot-c)"></i>WORKLINK</li>
    <li><i style="background:var(--dot-d)"></i>CIRCLES PLUS</li>
  </ul>

  <div class="footer-brand">Marrow Lane<small>Real Estate</small></div>
</footer>
<div class="abs copy">Copyright © 2016 Marrow Lane Real Estate. All rights reserved.</div>

</body>
</html>
```